Medical Billing Company Needs a Business Card Design

We need a business card design for a Florida based medical billing company called 'Clinicians Keystone Solutions'. We specialize in providing revenue cycle management services to physician and therapist offices (we're basically their back-office processing partner for providing billing software, claims submissions, A/R follow-up and patient statements & collections. Our logo is red and blue-ish, so make sure that whatever other elements are used will match appropriately. Our current business card design has a too small font size. I'd like to project an image that shows we are modern & reliable. On a side note, I'm planning on using ZUB for printing these cards.

Target Market(s)

Office managers, physicians, therapists

Industry/Entity Type

Printing

Requirements
Must have
• Logo
Name of Employee
Phone
Fax
E-mail
Website

```html
<!DOCTYPE html>
<html lang="en">
<head>
<meta charset="utf-8">
<title>Clinicians Keystone – Business Card</title>
<link rel="stylesheet" href="https://fonts.googleapis.com/css2?family=Open+Sans:wght@400;600;700&display=swap">
<style>
  :root{
    --bg:#e4e4ea;
    --card:#ffffff;
    --navy:#2c2380;
    --violet:#5a4aa6;
    --red:#a3151f;
    --ink:#4a4a4f;
    --rule:#c9c9cf;
  }
  *{box-sizing:border-box;margin:0;padding:0}
  html,body{width:1200px;height:987px;overflow:hidden}
  body{background:var(--bg);font-family:"Open Sans",Arial,sans-serif;position:relative}
  .card{position:absolute;left:220px;width:760px;height:434px;background:var(--card);
        border-radius:28px;overflow:hidden;box-shadow:0 6px 18px rgba(0,0,0,.15)}
  .card--back{top:30px}
  .card--front{top:523px}
  .brand-name{font-weight:600;color:var(--navy);letter-spacing:.04em;text-transform:uppercase;white-space:nowrap}
  .card--back .brand-name{position:absolute;left:0;right:0;top:150px;text-align:center;font-size:46px}
  .card--back .web{position:absolute;left:0;right:0;top:236px;text-align:center;font-size:22px;
        letter-spacing:.22em;color:var(--ink)}
  .card--front .brand-name{position:absolute;left:0;right:0;top:44px;text-align:center;font-size:38px}
  .accent-band{position:absolute;left:0;right:0;top:318px;bottom:0;
        background:linear-gradient(100deg,var(--navy) 0%,var(--violet) 45%,var(--navy) 100%)}
  .address{position:absolute;left:80px;top:150px;width:170px;text-align:right;font-size:17px;
        font-style:normal;line-height:1.45;color:var(--ink)}
  .divider{position:absolute;left:270px;top:150px;width:1px;height:140px;background:var(--rule)}
  .contacts{position:absolute;left:290px;top:146px;list-style:none;font-size:19px;line-height:1.55;color:var(--ink)}
  .contacts li{display:flex;align-items:center;gap:9px}
  .contacts svg{width:16px;height:16px;flex:none}
  .person{position:absolute;right:46px;bottom:26px;text-align:right;color:#fff}
  .person .name{font-size:32px;font-weight:700;line-height:1.1}
  .person .title{font-size:22px;font-weight:400}
</style>
</head>
<body>
  <section class="card card--back" aria-label="Card back">
    <p class="brand-name">Clinicians Keystone</p>
    <p class="web">www.clinicianskeystone.com</p>
  </section>

  <section class="card card--front" aria-label="Card front">
    <div class="accent-band" role="img" aria-label="Decorative swoosh in navy, red and purple"></div>

    <p class="brand-name">Clinicians Keystone</p>

    <address class="address">Street Name<br>City Name<br>State Zip Code</address>
    <span class="divider"></span>
    <ul class="contacts">
      <li><svg viewBox="0 0 16 16"><circle cx="8" cy="8" r="8" fill="var(--navy)"/><path d="M5 4.5l1.6-.5 1 2.3-1 .7a5 5 0 0 0 2.4 2.4l.7-1 2.3 1-.5 1.6C8 11.5 4.5 8 5 4.5z" fill="#fff"/></svg>123-456-0789</li>
      <li><svg viewBox="0 0 16 16"><rect x="4" y="1" width="8" height="14" rx="1.5" fill="var(--navy)"/><rect x="5.5" y="3" width="5" height="6" fill="#fff"/></svg>123-456-0789</li>
      <li><svg viewBox="0 0 16 16"><rect x="1" y="3" width="14" height="10" rx="1.5" fill="var(--navy)"/><path d="M2 4l6 5 6-5" fill="none" stroke="#fff" stroke-width="1.3"/></svg>info@clinicianskeystone.com</li>
      <li><svg viewBox="0 0 16 16"><circle cx="8" cy="8" r="7" fill="none" stroke="var(--navy)" stroke-width="1.5"/><path d="M1 8h14M8 1c-3 3-3 11 0 14M8 1c3 3 3 11 0 14" fill="none" stroke="var(--navy)" stroke-width="1.2"/></svg>www.clinicianskeystone.com</li>
    </ul>

    <div class="person">
      <p class="name">Your Name</p>
      <p class="title">Title</p>
    </div>
  </section>
</body>
</html>
```